Real Estate Webpage Design

We have an existing website: ferndaleestatecollective.com.au
We focus customised service mainly on Property Management and second-hand property sales.
We are not entirely happy about the current design and layout can stay roughly the same as the back end coding is linked to a CRM system.
We would like to see the design are more reachable to our clients and appearing.
Please check our Website Design Draft for more details.

Industry/Entity Type

Real estate Agency

Number of Pages Required

5+ page

Font styles to use
Sans Serif

Colors

Designer to choose colors to be used in the design.

```html
<!DOCTYPE html>
<html lang="en">
<head>
<meta charset="utf-8">
<title>Landlord – Ferndale Estate Collective</title>
<link href="https://fonts.googleapis.com/css2?family=Quicksand:wght@400;500;600;700&family=Roboto:wght@300;400;700&display=swap" rel="stylesheet">
<style>
:root{
  --gold:#f9b613;
  --navy:#15253a;
  --text:#1f2a37;
  --muted:#7a7f87;
  --cream:#fdfaf1;
  --grey:#f7f7f7;
  --line:#e3e3e3;
  --white:#ffffff;
}
*{margin:0;padding:0;box-sizing:border-box}
html,body{width:746px;height:1200px;overflow:hidden;background:var(--white)}
body{position:relative;font-family:"Quicksand",sans-serif;color:var(--text)}
.abs{position:absolute}
/* nav */
.site-nav{left:0;top:0;width:746px;height:37px;background:var(--white)}
.brand{left:37px;top:0;width:140px;height:47px;background:var(--white);z-index:3;display:flex;align-items:center;padding-left:11px;gap:6px}
.brand-mark{width:14px;height:14px;background:var(--gold);flex:none}
.brand-name{font-family:"Quicksand",sans-serif;font-weight:700;color:var(--gold);font-size:11px;line-height:1.05}
.menu{left:202px;top:14px;display:flex;gap:0;font-size:8.5px;font-weight:500}
.menu span{margin-right:17px;white-space:nowrap}
.menu .active{color:var(--gold);position:relative}
.menu .active:after{content:"";position:absolute;left:0;right:0;top:17px;height:1px;background:var(--gold)}
.btn{background:var(--gold);color:var(--white);font-size:8.5px;display:flex;align-items:center;justify-content:center;border-left:1px solid var(--navy);border-top:1px solid var(--navy)}
.add-btn{left:630px;top:11px;width:79px;height:22px}
/* hero */
.hero{left:0;top:37px;width:746px;height:220px;background:linear-gradient(100deg,#2f3b27 0%,#4a5a44 30%,#7e8f9c 55%,#4f6b3e 80%,#35522b 100%)}
.hero-title{left:38px;top:121px;font-family:"Roboto",sans-serif;font-weight:700;font-size:24px;color:var(--gold)}
.hero-sub{left:38px;top:157px;font-family:"Roboto",sans-serif;font-size:8px;color:var(--white)}
/* service */
.service{left:37px;top:247px;width:672px;height:203px;background:var(--cream);text-align:center;padding:26px 138px 0}
.service h1{font-family:"Roboto",sans-serif;font-weight:700;font-size:20px;color:var(--navy);margin-bottom:12px}
.service p{font-size:8.5px;line-height:14px;color:var(--muted);margin-bottom:8px}
/* testimonial */
.quote-head{left:0;width:766px;top:496px;text-align:center;font-family:"Roboto",sans-serif;font-weight:700;font-size:17px;color:var(--navy)}
.quote-mark{left:371px;top:531px}
.quote-text{left:223px;top:561px;width:320px;text-align:center;font-family:"Roboto",sans-serif;font-weight:300;font-size:8.2px;line-height:14px;color:var(--muted)}
.quote-name{left:0;width:768px;top:643px;text-align:center;font-family:"Roboto",sans-serif;font-size:8px;color:var(--text)}
.quote-role{left:0;width:768px;top:656px;text-align:center;font-size:8.5px;color:var(--gold)}
.arrow{width:24px;height:24px;display:flex;align-items:center;justify-content:center}
.arrow-prev{left:135px;top:597px;background:var(--gold)}
.arrow-next{left:587px;top:597px;border:1px solid var(--gold);background:var(--white)}
/* advantages */
.advantages{left:0;top:719px;width:746px;height:274px;background:var(--grey)}
.adv-head{left:0;width:746px;top:751px;text-align:center;font-family:"Roboto",sans-serif;font-weight:700;font-size:17px;color:var(--navy)}
.adv{top:788px;width:150px;text-align:center}
.adv svg{display:block;margin:0 auto 6px}
.adv h3{font-family:"Roboto",sans-serif;font-weight:400;font-size:10px;color:var(--text);margin-bottom:5px}
.adv p{font-family:"Roboto",sans-serif;font-weight:300;font-size:8px;line-height:14px;color:var(--muted)}
.switch-btn{left:342px;top:940px;width:62px;height:21px}
/* footer */
.foot-brand{left:37px;top:1018px;display:flex;align-items:center;gap:6px}
.foot-brand .brand-mark{width:16px;height:16px}
.foot-brand .brand-name{font-size:12px}
.foot-about{left:38px;top:1057px;width:125px;font-size:8px;line-height:14px}
.foot-title{font-size:8.5px;color:var(--gold);top:1016px}
.sitemap{left:209px;top:1034px;font-size:7.5px;font-weight:500;line-height:18.5px}
.contact{left:380px;top:1035px;font-size:7.5px;font-weight:500}
.contact .row{display:flex;gap:8px;margin-bottom:8px;line-height:12px}
.contact b{font-weight:700}
.socials{left:553px;top:1038px;display:flex;gap:9px}
.socials span{width:24px;height:24px;border-radius:50%;border:1px solid var(--gold)}
.socials span:first-child{background:var(--gold)}
.bottom-line{left:0;top:1177px;width:746px;height:1px;background:var(--line)}
.copy{left:38px;top:1183px;font-size:7.5px;font-weight:500}
.legal{right:38px;top:1183px;font-size:7.5px;font-weight:500;display:flex;gap:14px}
</style>
</head>
<body>
<header class="abs site-nav"></header>
<div class="abs brand"><span class="brand-mark"></span><span class="brand-name">Ferndale<br>Estate Collective</span></div>
<nav class="abs menu">
  <span>Home</span><span>About Us</span><span class="active">Landload</span><span>Tenant</span><span>Make a Switch</span><span>Property Sales</span><span>Appraisal now</span>
</nav>
<div class="abs btn add-btn">Add Properties</div>

<section class="abs hero" role="img" aria-label="Modern two-storey timber and dark-clad house surrounded by tall green trees and lawn"></section>
<h2 class="abs hero-title">Landlord</h2>
<p class="abs hero-sub">Your local real estate property group</p>

<section class="abs service">
  <h1>Our Property&nbsp; Managment Service</h1>
  <p>Lorem Ipsum is simply dummy text of the printing and typesetting industry. Lorem Ipsum has been the industry's standard dummy text ever since the 1500s, when an unknown printer took a galley of type and scrambled it to make a type specimen book. It has survived not only five centuries, but also the leap into electronic typesetting, remaining essentially unchanged.</p>
  <p>It was popularised in the 1960s with the release of Letraset sheets containing Lorem Ipsum passages, and more recently with desktop publishing software like Aldus PageMaker including versions of Lorem Ipsum.</p>
</section>

<h2 class="abs quote-head">What our senior property manager says</h2>
<svg class="abs quote-mark" width="26" height="22" viewBox="0 0 26 22"><path d="M1 21V13C1 6 4 2 10 0l1 3C7 5 6 8 6 10h5v11zM15 21V13c0-7 3-11 9-13l1 3c-4 2-5 5-5 7h5v11z" fill="#f9b613"/></svg>
<p class="abs quote-text">Lorem Ipsum is simply dummy text of the printing and typesetting industry. Lorem Ipsum has been the industry's standard dummy text ever since the 1500s, when an unknown printer took a galley of type and scrambled it to make a type specimen book. It has survived not only five centuries, but also the leap into electronic typesetting, remaining essentially unchanged.</p>
<p class="abs quote-name">Mara Lindqvist</p>
<p class="abs quote-role">Director and Property Manager</p>
<div class="abs arrow arrow-prev"><svg width="10" height="14" viewBox="0 0 10 14"><path d="M8 1 2 7l6 6" stroke="#fff" stroke-width="1.4" fill="none"/></svg></div>
<div class="abs arrow arrow-next"><svg width="10" height="14" viewBox="0 0 10 14"><path d="M2 1l6 6-6 6" stroke="#15253a" stroke-width="1.4" fill="none"/></svg></div>

<section class="abs advantages"></section>
<h2 class="abs adv-head">Our advantage</h2>
<div class="abs adv" style="left:37px">
  <svg width="36" height="34" viewBox="0 0 36 34" fill="none" stroke="#15253a" stroke-width="1.3"><circle cx="9" cy="20" r="3.5"/><circle cx="18" cy="17" r="4"/><circle cx="27" cy="20" r="3.5"/><path d="M3 32c0-4 3-7 6-7M33 32c0-4-3-7-6-7M10 32c0-5 4-9 8-9s8 4 8 9z"/><path d="M18 2l1.2 2.6 2.8.3-2 1.9.5 2.8L18 8.2l-2.5 1.4.5-2.8-2-1.9 2.8-.3zM7 6l.8 1.6 1.7.2-1.2 1.2.3 1.7L7 9.9l-1.6.8.3-1.7-1.2-1.2 1.7-.2zM29 6l.8 1.6 1.7.2-1.2 1.2.3 1.7-1.6-.8-1.6.8.3-1.7-1.2-1.2 1.7-.2z" stroke="#f9b613"/></svg>
  <h3>Great Experience</h3>
  <p>Lorem Ipsum is simply dummy text of the printing and typesetting industry. Lorem Ipsum has been the industry's standard dummy text.</p>
</div>
<div class="abs adv" style="left:212px">
  <svg width="36" height="34" viewBox="0 0 36 34" fill="none" stroke="#15253a" stroke-width="1.3"><rect x="12" y="2" width="12" height="12" stroke="#f9b613"/><path d="M15 6h2M19 6h2M15 10h2M19 10h2" stroke="#f9b613"/><path d="M1 18h5v12H1zM30 18h5v12h-5zM6 20l6-3 6 3 6-3 6 3M6 28l4 0 6 4 4-2 6-2h4M12 22l4 4 4-2"/></svg>
  <h3>Safety Deals</h3>
  <p>Lorem Ipsum is simply dummy text of the printing and typesetting industry. Lorem Ipsum has been the industry's standard dummy text.</p>
</div>
<div class="abs adv" style="left:383px">
  <svg width="36" height="34" viewBox="0 0 36 34" fill="none" stroke="#15253a" stroke-width="1.3"><circle cx="17" cy="15" r="5"/><path d="M10 26c1-4 4-6 7-6s6 2 7 6M6 16a11 11 0 0 1 19-8M29 14a11 11 0 0 1-6 13"/><rect x="25" y="2" width="9" height="6" stroke="#f9b613"/><path d="M4 22l3-2 2 4-2 1c1 2 2 3 4 4l1-2 4 2-2 3c-5-1-9-5-10-10z" stroke="#f9b613"/></svg>
  <h3>Comprehensive Support</h3>
  <p>Lorem Ipsum is simply dummy text of the printing and typesetting industry. Lorem Ipsum has been the industry's standard dummy text.</p>
</div>
<div class="abs adv" style="left:555px">
  <svg width="36" height="34" viewBox="0 0 36 34" fill="none" stroke="#15253a" stroke-width="1.3"><path d="M8 14l5-6 5 6v7H8zM20 10h10v11H20z" stroke="#f9b613"/><path d="M2 20h4v13H2zM6 23h10c2 0 3 2 1 3h-7M6 31h14l12-7c1-2-1-3-3-2l-7 4"/></svg>
  <h3>Property Management</h3>
  <p>Lorem Ipsum is simply dummy text of the printing and typesetting industry. Lorem Ipsum has been the industry's standard dummy text.</p>
</div>
<div class="abs btn switch-btn">Switch Now</div>

<footer>
  <div class="abs foot-brand"><span class="brand-mark"></span><span class="brand-name">Ferndale<br>Estate Collective</span></div>
  <p class="abs foot-about">Lorem ipsum dolor sit amet, consectetur adipiscing elit, sed do eiusmod tempor...</p>

  <p class="abs foot-title" style="left:206px">Site Map</p>
  <div class="abs sitemap">Home<br>About Us<br>Landload<br>Tenant<br>Make a Switch<br>Property Sales<br>Appraisal now</div>

  <p class="abs foot-title" style="left:381px">Contact Us</p>
  <div class="abs contact">
    <div class="row"><svg width="13" height="14" viewBox="0 0 13 14" fill="none" stroke="#15253a"><path d="M6.5 13S2 8 2 5a4.5 4.5 0 0 1 9 0c0 3-4.5 8-4.5 8z"/><circle cx="6.5" cy="5" r="1.6"/></svg><span>18/4 Wattle Crest Rd,<br>Belconnen, ACT, 2617</span></div>
    <div class="row"><svg width="13" height="14" viewBox="0 0 13 14" fill="none" stroke="#15253a"><path d="M2 2l3-1 2 3-2 1c1 2 2 3 4 4l1-2 3 2-1 3C6 12 2 8 2 2z"/></svg><span><b>02 6190 3327</b><br><b>02 6152 7741</b></span></div>
    <div class="row"><svg width="14" height="12" viewBox="0 0 14 12" fill="none" stroke="#15253a"><rect x="1" y="1" width="12" height="10"/><path d="M1 1l6 5 6-5"/></svg><span>info@ferndaleestate.com</span></div>
  </div>

  <p class="abs foot-title" style="left:553px">Social Media</p>
  <div class="abs socials" aria-label="Social media links"><span></span><span></span><span></span><span></span></div>

  <div class="abs bottom-line"></div>
  <p class="abs copy">2022© Ferndale Estate Collective. All right reserved.</p>
  <div class="abs legal"><span>Privacy</span><span>Complaint Handling &amp; Dispute Resolution</span><span>Due Diligence Checklist</span></div>
</footer>
</body>
</html>
```